Wordpress Design Project

Hi,

I would like a more modern colourful design doing for my website ZAP Lnx (www.za%plnx.com - remove percentage). But I do still want to keep the same sort of colors, just maybe lighter. More interesting.

I want the inside pages to NOT all look the same with just boring text.

I want the site to look more appealing and maybe a new logo.
Updates

I would like to mention I would prefer to keep the same logo after rethinking it (possibly a slight refresh of the logo if you feel its a good idea) and the same color scheme as at present.

Saves us rebranding a lot of our apps, tools online ads etc.

Also I thought it is worth mentioning we have 2 parts to the site. The front end and the logged in area. It would be good if when making the front end you keep in mind the back end at http://p.za%plnx.com (remove percentage). We can only edit this limitedly (can edit the entire footer, the logo and full CSS of it). Would be good if we could make sure the header and footer can be used on the back end as well maybe to make it match.

I also want layouts making not just for the homepage. Obviously every page will basically be the same but I don't want all the other pages to just be 'text' and no real layout.

You can see out main pages on the website at the moment, I want those other pages to be laid out nice and differently as well. For example the testimonials page could be more interesting with speech bubbles and pictures of each person (just use placeholders). The affiliates page could be a description and then a nice fancy list of features why to join etc. 

Nothing overly complicated but I think it makes the whole site seem a lot better.

Target Market(s)

Affiliate Marketing. International.

Requirements
Must have
• Needs to be more room for links across the navigation at the top, also sub menus (at present we have a lot of pages which are hidden deep within other pages).
Nice to have
• Lists of features for advertisers and affiliates on the homepage part.

Menu items and buttons have nice hover over effects.

I want to get across on our pages all the different unique features we have.

Maybe some kind of slider which has past offer logos in, just use example logos.

```html
<!DOCTYPE html>
<html lang="en">
<head>
<meta charset="utf-8">
<title>ZAP Lnx – About Us</title>
<link href="https://fonts.googleapis.com/css2?family=Signika:wght@400;600&family=Arimo:wght@400&family=Roboto+Condensed:wght@400;700&display=swap" rel="stylesheet">
<style>
:root{
  --orange:#f7931e;
  --orange-dark:#e5780a;
  --orange-light:#ffab3d;
  --teal:#4fd0dc;
  --teal-text:#1fb5c6;
  --text:#7d7d7d;
  --dark:#1b1b1b;
  --panel:#eeeeee;
  --rule:#e2e2e2;
  --footer:#e9eff0;
  --social:#5a7fa3;
  --white:#ffffff;
}
*{box-sizing:border-box;margin:0;padding:0}
html,body{width:1130px;height:1200px;overflow:hidden;background:var(--white);font-family:"Arimo",Arial,sans-serif;color:var(--text)}
a{text-decoration:none;color:inherit}
h1,h2,h3{font-weight:400}
.wrap{width:847px;margin-left:141px;position:relative}

/* header */
.site-header{height:97px;position:relative}
.brand{position:absolute;left:20px;top:24px;display:flex;align-items:center;gap:12px}
.brand-mark{width:18px;height:18px;background:var(--orange)}
.brand-name{font-family:"Signika",sans-serif;font-weight:600;font-size:44px;color:var(--dark);line-height:1}
.header-actions{position:absolute;right:0;top:15px;display:flex;gap:10px}
.btn-head{background:linear-gradient(var(--orange-light),var(--orange-dark));color:var(--white);font-family:"Signika",sans-serif;font-size:15px;padding:5px 12px;border-radius:5px;box-shadow:0 2px 0 #b85a00}
.phone{position:absolute;right:0;top:58px;font-family:"Roboto Condensed",sans-serif;font-weight:700;font-size:24px;color:var(--dark)}

/* nav */
.main-nav{height:34px;background:linear-gradient(var(--orange-light),var(--orange) 60%,var(--orange-dark));border-bottom:1px solid #fff}
.main-nav ul{list-style:none;display:flex;height:34px;margin-left:158px}
.main-nav li a{display:block;height:34px;line-height:34px;padding:0 7px;color:var(--white);font-family:"Signika",sans-serif;font-size:18px;margin-right:16px}
.main-nav li.is-active a{background:var(--teal)}

/* title band */
.page-band{height:70px;background:var(--teal)}
.page-band .wrap{height:70px;display:flex;align-items:center;justify-content:space-between}
.page-title{font-family:"Signika",sans-serif;font-weight:600;font-size:35px;color:var(--white);letter-spacing:.5px}
.band-map{width:85px;height:40px;margin-right:20px;border-radius:14px;background:rgba(255,255,255,.35)}

/* body */
.content{display:flex;gap:35px;padding-top:33px;height:845px}
.sidebar{width:200px;flex:none}
.login-box{background:var(--panel);border-radius:6px;padding:14px 18px 16px}
.side-title{font-family:"Roboto Condensed",sans-serif;font-size:20px;color:var(--dark);text-transform:uppercase;margin-bottom:12px}
.field{display:block;height:36px;background:var(--white);border-radius:6px;padding:0 10px;line-height:36px;font-size:13px;color:var(--dark);margin-bottom:18px}
.forgot{font-size:12px;color:var(--dark);margin:-4px 0 18px 2px}
.login-row{display:flex;align-items:center;gap:8px;font-size:12px;color:var(--dark)}
.btn-login{border:1px solid #bbb;border-radius:5px;background:linear-gradient(#fafafa,#ddd);padding:5px 8px;font-family:"Signika",sans-serif;font-weight:600;font-size:14px;color:var(--dark)}
.side-block{margin-top:30px}
.post-list{list-style:none;border-bottom:2px solid var(--rule);padding-bottom:8px}
.post-list li{font-size:13px;padding:5px 0 6px 12px;border-bottom:1px solid var(--rule);position:relative}
.post-list li:last-child{border-bottom:0}
.post-list li::before{content:"›";position:absolute;left:0;top:3px}
.social{display:flex;gap:15px;margin-top:4px}
.social-link{width:37px;height:39px;border-radius:5px;background:var(--social);display:flex;align-items:center;justify-content:center}

.main{width:612px;font-size:13.4px;line-height:17.7px}
.main p{margin-bottom:17.7px}
.main a{color:var(--teal-text)}
.team-title{font-family:"Roboto Condensed",sans-serif;font-size:21px;color:var(--teal-text);margin:40px 0 6px}
.member{display:flex;gap:15px;padding-bottom:22px;margin-bottom:20px;border-bottom:1px solid var(--rule)}
.member:last-child{border-bottom:0}
.photo{width:115px;height:141px;flex:none;background:#fff;border:6px solid #eee;box-shadow:3px 3px 4px rgba(0,0,0,.18)}
.photo div{width:100%;height:100%;background:linear-gradient(#e2e6e7,#cfd5d6)}
.member-name{font-size:19px;color:var(--dark);margin-top:-2px}
.member-role{font-size:14px;margin-bottom:10px!important}
.member-bio{line-height:20px}

/* badges */
.apps{display:flex;justify-content:center;gap:20px;height:60px}
.app{width:127px;height:36px;border:2px solid #d6e4ec;display:flex;align-items:center;gap:6px;padding:0 6px}
.app-mark{width:24px;height:24px;border-radius:50%;flex:none}
.app b{display:block;font-size:10px;color:#3c7dab;line-height:11px}
.app small{display:block;font-size:6px;color:#555;line-height:8px}

/* footer */
.site-footer{background:var(--footer);border-top:15px solid #dde6e8;height:94px;text-align:center;padding-top:16px}
.footer-links{font-size:12.5px;color:var(--dark)}
.footer-links span{margin:0 20px}
.copyright{font-size:12px;margin-top:12px;color:#6b6b6b}
</style>
</head>
<body>
<header class="site-header wrap">
  <div class="brand"><span class="brand-mark"></span><span class="brand-name">ZAP Lnx</span></div>
  <div class="header-actions"><a class="btn-head" href="#">LOGIN</a><a class="btn-head" href="#">SING UP</a></div>
  <div class="phone">+44 (0)1632 960418</div>
</header>

<nav class="main-nav">
  <ul>
    <li><a href="#">HOME</a></li>
    <li class="is-active"><a href="#">ABOUT US</a></li>
    <li><a href="#">OUR BLOG</a></li>
    <li><a href="#">TESTIMONIALS</a></li>
    <li><a href="#">AFFILIATES</a></li>
    <li><a href="#">ADVERTISERS</a></li>
    <li><a href="#">CONTACT US</a></li>
  </ul>
</nav>

<section class="page-band">
  <div class="wrap">
    <h1 class="page-title">ABOUT US</h1>
    <div class="band-map" role="img" aria-label="Faint world map decoration"></div>
  </div>
</section>

<div class="content wrap">
  <aside class="sidebar">
    <div class="login-box">
      <h2 class="side-title">Account Login</h2>
      <span class="field">Email</span>
      <span class="field">Password</span>
      <p class="forgot">Forgot Password</p>
      <div class="login-row"><span class="btn-login">LOGIN</span> or Sign Up</div>
    </div>
    <div class="side-block">
      <h2 class="side-title">Recent Blog Posts</h2>
      <ul class="post-list">
        <li>New Offers For China</li>
        <li>NEW: Banner Rotators</li>
        <li>New Offers</li>
      </ul>
    </div>
    <div class="side-block">
      <h2 class="side-title">Social Networking</h2>
      <div class="social">
        <a class="social-link" href="#" aria-label="Share"><svg width="20" height="20" viewBox="0 0 20 20"><circle cx="5" cy="10" r="2.5" fill="#fff"/><circle cx="15" cy="4" r="2.5" fill="#fff"/><circle cx="15" cy="16" r="2.5" fill="#fff"/><path d="M5 10L15 4M5 10L15 16" stroke="#fff" stroke-width="1.6"/></svg></a>
        <a class="social-link" href="#" aria-label="Message"><svg width="20" height="20" viewBox="0 0 20 20"><path d="M3 4h14v9H8l-4 3v-3H3z" fill="#fff"/></svg></a>
        <a class="social-link" href="#" aria-label="Video"><svg width="20" height="20" viewBox="0 0 20 20"><path d="M7 5l8 5-8 5z" fill="#fff"/></svg></a>
        <a class="social-link" href="#" aria-label="Profile"><svg width="20" height="20" viewBox="0 0 20 20"><circle cx="10" cy="7" r="3.5" fill="#fff"/><path d="M3.5 17c0-4 3-6 6.5-6s6.5 2 6.5 6z" fill="#fff"/></svg></a>
      </div>
    </div>
  </aside>

  <main class="main">
    <p>ZAP Lnx, which started in 2007 is a powerful performance-based internet marketing network dedicated to advertisers to consumers through its powerful international affiliate network.</p>
    <p>For Advertisers, we offer an extensive network of website and e-mail distribution. Our network currently advertise a range of companies in all kinds of industries. Advertisers pay only for the results they achieve on a cost per click, cost per lead, cost per acquisition, or cost per impression basis, as well as combinations of those models. So you only pay when you get a ‘real’ result, we take the risk out of advertising.</p>
    <p>For website owners (affiliates), ZAP Lnx generates high revenues per impression promoting compelling offers from quality brands in graphical formats that complement the affiliates’ sites and add value for their customers. We have many exclusive offers with high payouts in a range of categories so you are sure to find something relevant to promote for your traffic. Start monetizing your traffic today!</p>
    <p>For email list owners, you can also sign up to ZAP Lnx for offers to promote to your email marketing lists. However we also have list management services, for more information <a href="#">click here.</a></p>
    <p>If at any time you require assistant, simply contact your account manager or <a href="#">click here</a> to contact our support team.</p>
    <p>Want to meet us before joining? <a href="#">Click here</a> to find out what upcoming events we are attending.</p>

    <h2 class="team-title">KEY TEAM</h2>
    <article class="member">
      <div class="photo"><div role="img" aria-label="Portrait placeholder of the managing director"></div></div>
      <div>
        <h3 class="member-name">Dan Whitfield</h3>
        <p class="member-role">Managing Director</p>
        <p class="member-bio">Dan is an experienced director, starting his first online marketing company at just 13. He has over 8 years experience in internet marketing and has been managing Lumen Media for over 5 years now.</p>
      </div>
    </article>
    <article class="member">
      <div class="photo"><div role="img" aria-label="Portrait placeholder of the affiliate manager"></div></div>
      <div>
        <h3 class="member-name">Helen Carrow</h3>
        <p class="member-role">Affiliate Manager</p>
        <p class="member-bio">Helen is very passionate about ZAP Lnx and is available to help affiliates and advertisers with any questions they may have.</p>
      </div>
    </article>
  </main>
</div>

<div class="apps">
  <div class="app"><span class="app-mark" style="background:#2d3b47;border-radius:3px;width:16px"></span><div><b>Mobile Stats</b><small>ZAP Lnx Mobile Website</small></div></div>
  <div class="app"><span class="app-mark" style="background:#e8742a"></span><div><b>Ember Browser</b><small>Official ZAP Lnx Extension</small></div></div>
  <div class="app"><span class="app-mark" style="background:#d9a22b"></span><div><b>Orbit Browser</b><small>Official ZAP Lnx Extension</small></div></div>
  <div class="app"><span class="app-mark" style="background:#8fbf3a;border-radius:3px"></span><div><b>Robo App</b><small>Official ZAP Lnx App</small></div></div>
</div>

<footer class="site-footer">
  <div class="footer-links">Affiliate Terms &amp; Conditions<span>|</span>Advertiser Terms &amp; Conditions<span>|</span>Privacy Policy &amp; Cookies<span>|</span>FAQ<span>|</span>Contact Us</div>
  <p class="copyright">© 2013 Lumen Media UK Ltd - All Rights Reserved.</p>
</footer>
</body>
</html>
```